Baby Cloth Business Needs a Web Design

We need a web design for a new company that produces and sells baby sleeping bags. We use kelvoTrade (demo.kelvotrade.example) e-commerce software which we need a new design for that represents our products better. We would like to see designs that use simple and clean elements, playful layout with big pictures and emphasis on typography. We already have a logo that is "fresh" apple green so we would like colors that go well with that.
We use the following pages/features:
- Home page (with newsletter, chatterbook link and contact us link)
- Category page (no search needed)
- Product details page (with share)
- User pages (register, login, my account)
- Shopping cart with all its pages (about 6-7)
- Static pages (3 pages: contact us, about us, conditions of use).

We need designs in the form of PSD

Target Market(s)

Primary: mothers 25-45; secondary: women 20-60 who buy it as gift

Industry/Entity Type

Business

Requirements
Must have
• Since the site uses kelvoTrade no other data can be added beside those already exist on site.
Nice to have
• We have photos taken for this site (sample attached) and would be nice to show them in big sizes. We would like to see imaginative, playful elements that appear several places throughout the site. Logo contains a small baby foot which could leave footprints here and there.

We like these sites (and what):
- http://www.pelora.example/13-organic-bamboo-cotton-baby-essentials (simple, nice but too gray)
- http://www.quindeco.example/ (logo placement, menu, background)
- http://www.tervalo.example/
- http://www.brelt.example/website-template/view/html/baby-clothes?originUrl=http%3A%2F%2Fwww.brelt.example%2Fwebsite%2Ftemplates%2Fhtml%2Fonline-shop%2F2&galleryDocIndex=0 (layout, image sizes)
- http://themes.fashion.kel-layouts.example/?isOpen=false&;t_r=true (layout)
Should not have
• We do not use forum, blog, new products, manufacturers, popular tags, polls, search from kelvoTrade.

```html
<!DOCTYPE html>
<html lang="en">
<head>
<meta charset="utf-8">
<title>Nestlyn – Baby Sleeping Bags</title>
<link href="https://fonts.googleapis.com/css2?family=Open+Sans:wght@400;600;700&family=Handlee&family=Oswald:wght@400;500&display=swap" rel="stylesheet">
<style>
:root{
  --green:#7db43f;
  --green-dark:#5aa00a;
  --green-light:#92d20a;
  --green-text:#78b52b;
  --ink:#333;
  --muted:#555;
  --line:#dcdcdc;
  --hero:#c0b5a6;
  --yellow:#f3f400;
  --white:#fff;
}
*{box-sizing:border-box;margin:0;padding:0}
html,body{width:1131px;height:1200px;overflow:hidden;background:var(--white)}
body{font-family:"Open Sans",Arial,sans-serif;color:var(--ink)}
.page{position:relative;width:1200px;height:1273px;transform:scale(.9425);transform-origin:0 0}
.abs{position:absolute}
.script{font-family:"Handlee",cursive}

.topbar{left:0;top:0;width:1200px;height:42px;background:var(--green);color:var(--white);font-size:13px}
.topbar span,.topbar svg{position:absolute;top:13px}
.topbar svg{top:12px}

.brand{left:128px;top:60px}
.brand-name{font-size:52px;font-weight:400;color:var(--green-text);line-height:1;display:flex;align-items:center;gap:10px}
.brand-dot{width:40px;height:40px;border:4px solid var(--green-text);border-radius:50%}
.brand-tag{font-size:7px;color:var(--green-text);margin:10px 0 0 42px}

.search{left:813px;top:55px;width:258px;height:24px;background:#f0f0f0;border-radius:3px;font-size:10px;color:#b5b5b5;padding:6px 4px}
.search svg{position:absolute;right:10px;top:3px}

.nav{top:114px;font-size:19px;color:#333}
.nav-sep{top:116px;width:1px;height:18px;background:#555}

.hero{left:120px;top:168px;width:961px;height:344px;background:var(--hero)}
.hero-photo{position:absolute;left:0;top:0;width:540px;height:344px;background:linear-gradient(100deg,#b57a48 0%,#caa284 45%,#e9d7c8 70%,#c0b5a6 100%)}
.hero-title{left:572px;top:98px;font-size:31px;color:var(--white);letter-spacing:1px}
.hero-copy{left:572px;top:148px;width:350px;font-size:12.5px;line-height:24px;color:var(--white)}
.dots{left:854px;top:301px;display:flex;gap:3px}
.dots i{width:13px;height:13px;border-radius:50%;background:#3a3a3a;border:1px solid #eee}
.dots i:first-child{background:var(--white);border:2px solid #333}

.section-title{font-size:22px;color:#333;letter-spacing:1px}

.card{width:221px}
.card-frame{position:relative;height:142px;border:1px solid var(--line);background:var(--white)}
.card-photo{position:absolute;top:12px;width:72px;height:118px;border-radius:20px}
.sale-tag{position:absolute;left:6px;top:12px;width:46px;height:36px;background:var(--green);color:var(--white);font-size:12px;text-align:center;line-height:36px;transform:rotate(-35deg);border-radius:4px}
.sale-foot{position:absolute;left:12px;top:58px;width:40px;height:68px;border:3px solid var(--green);border-radius:20px 20px 22px 22px;font-size:11px;text-align:center;padding-top:13px;line-height:15px;color:#333}
.sale-foot b{color:#3c7d08;font-weight:700}
.card-name{margin-top:8px;font-size:12px;font-weight:700;color:var(--green-text)}
.card-desc{margin-top:6px;font-size:12.5px;line-height:20px;color:var(--muted);width:200px}
.card-price{font-size:19px;font-weight:600;color:#222;line-height:24px}
.card-actions{margin-top:11px;display:flex;justify-content:space-between}
.btn{width:105px;height:34px;color:var(--white);font-size:13px;font-weight:600;text-align:center;line-height:34px}
.btn-cart{background:var(--green-dark)}
.btn-info{background:var(--green-light)}

.promo{top:947px;width:267px;height:171px;background:var(--white);box-shadow:2px 4px 8px rgba(0,0,0,.25)}
.new-photo{position:absolute;left:12px;top:16px;width:116px;height:140px;background:linear-gradient(160deg,#5b6a63,#3b4742);border-radius:30px 30px 20px 20px}
.new-panel{position:absolute;left:132px;top:0;width:135px;height:171px;background:var(--green);font-family:"Oswald",sans-serif;color:var(--white);padding:38px 0 0 16px;line-height:1}
.new-panel .l1{font-size:21px}
.new-panel .l1 em{font-style:normal;color:var(--yellow)}
.new-panel .l2{font-size:21px;color:var(--yellow)}
.new-panel .l3{font-size:50px;margin-top:4px}
.buy{position:absolute;left:6px;bottom:6px;width:100px;height:28px;background:var(--yellow);color:#111;font-family:"Handlee",cursive;font-size:20px;text-align:center;line-height:28px;font-weight:700}

.nl-head{left:57px;top:20px;font-family:"Oswald",sans-serif;font-size:20px;color:var(--green-text);letter-spacing:-.3px}
.nl-copy{left:21px;top:52px;width:234px;font-size:8px;line-height:16px;color:#aaa}
.nl-input{left:24px;top:89px;width:225px;height:34px;border:1px solid #ccc;border-top:2px solid #bbb;background:#f2f2f2;font-size:12px;color:#aaa;padding:9px 8px}
.nl-submit{left:169px;top:133px;width:82px;height:23px;background:var(--yellow);font-size:9px;font-weight:600;text-align:center;line-height:23px;color:#222}

.offer-photo{position:absolute;left:0;top:0;width:267px;height:171px;background:linear-gradient(180deg,#c9ccc6 0%,#b9b2a4 55%,#d5cdbf 100%)}
.offer-badge{position:absolute;left:0;top:41px;width:103px;height:130px;background:var(--green);border-radius:0 65px 0 0;font-family:"Oswald",sans-serif;color:var(--white);padding:26px 0 0 9px;line-height:1}
.offer-badge .o1{font-size:26px}
.offer-badge .o2{font-size:16px;color:var(--yellow);margin-top:2px}
.offer-badge .o3{font-size:40px;margin-top:3px}

.footer{left:0;top:1178px;width:1200px;height:95px;background:var(--green);color:var(--white)}
.foot-links{left:129px;top:22px;font-size:12.5px;display:flex;gap:0}
.foot-links span{padding:0 8px}
.foot-links span:first-child{padding-left:0}
.foot-copy{left:131px;top:53px;font-size:13px}
.social{left:918px;top:30px;display:flex;gap:9px}
.social i{width:31px;height:31px;border-radius:50%;background:var(--white)}
</style>
</head>
<body>
<div class="page">

  <header>
    <div class="abs topbar">
      <span style="left:550px">Welcome&nbsp;&nbsp;:</span>
      <svg style="left:625px" width="20" height="18" viewBox="0 0 20 18" aria-hidden="true"><path d="M2 6h16l-2 10H4z" fill="none" stroke="#fff" stroke-width="2"/><path d="M6 6l4-5 4 5" fill="none" stroke="#fff" stroke-width="1.6"/></svg>
      <span style="left:652px">Shopping Bag: (empty)</span>
      <svg style="left:803px" width="14" height="17" viewBox="0 0 14 17" aria-hidden="true"><circle cx="7" cy="5" r="4" fill="#fff"/><path d="M0 16c0-5 3-7 7-7s7 2 7 7z" fill="#fff"/></svg>
      <span style="left:825px">Your Account</span>
      <span style="left:915px">|</span>
      <svg style="left:928px" width="12" height="16" viewBox="0 0 12 16" aria-hidden="true"><path d="M3 7V4a3 3 0 016 0v3" fill="none" stroke="#fff" stroke-width="2"/><rect x="0" y="7" width="12" height="9" fill="#fff"/></svg>
      <span style="left:946px">Login</span>
      <svg style="left:991px;top:14px" width="27" height="16" viewBox="0 0 27 16" aria-label="English flag" role="img"><rect width="27" height="16" fill="#1f3f8f"/><path d="M0 0L27 16M27 0L0 16" stroke="#fff" stroke-width="3"/><path d="M13.5 0v16M0 8h27" stroke="#fff" stroke-width="5"/><path d="M13.5 0v16M0 8h27" stroke="#c8102e" stroke-width="3"/></svg>
      <span style="left:1025px">English&nbsp;&nbsp;<span style="position:static;color:#4d7a20">▼</span></span>
    </div>

    <div class="abs brand">
      <div class="brand-name"><span class="brand-dot"></span>Nestlyn</div>
      <div class="brand-tag">smart sleeping bag for babies and kids</div>
    </div>

    <div class="abs search">Search
      <svg width="20" height="20" viewBox="0 0 20 20" aria-hidden="true"><circle cx="8" cy="8" r="6" fill="none" stroke="#999" stroke-width="2.4"/><path d="M12.5 12.5l6 6" stroke="#999" stroke-width="3"/></svg>
    </div>

    <nav>
      <span class="abs nav script" style="left:443px">Home</span>
      <i class="abs nav-sep" style="left:509px"></i>
      <span class="abs nav script" style="left:536px">About Us</span>
      <i class="abs nav-sep" style="left:641px"></i>
      <span class="abs nav script" style="left:663px">Sleeping Bags</span>
      <i class="abs nav-sep" style="left:793px"></i>
      <span class="abs nav script" style="left:814px">Gifts</span>
      <i class="abs nav-sep" style="left:880px"></i>
      <span class="abs nav script" style="left:909px">Sale</span>
      <i class="abs nav-sep" style="left:960px"></i>
      <span class="abs nav script" style="left:982px">Contact Us</span>
    </nav>
  </header>

  <section class="abs hero">
    <div class="hero-photo" role="img" aria-label="Photo of a smiling toddler in a blue polka-dot sleeping bag sitting in a wooden chair"></div>
    <h1 class="abs hero-title script" style="font-weight:400">Baby Slepping Bags</h1>
    <p class="abs hero-copy">ed ut perspiciatis unde omnis iste natus error sit voluptatem accusantium doloremque laudantium, totam rem aperiam, eaque ipsa quae ab illo inventore veritatis et quasi architecto beatae vitae dicta sunt explicabo.</p>
    <div class="abs dots"><i></i><i></i><i></i><i></i></div>
  </section>

  <section>
    <h2 class="abs section-title script" style="left:538px;top:539px;font-weight:400">Our Products</h2>
    <svg class="abs" style="left:133px;top:555px" width="20" height="28" viewBox="0 0 20 28" aria-label="Previous" role="img"><path d="M17 2L4 14l13 12" fill="none" stroke="#999" stroke-width="3"/></svg>
    <svg class="abs" style="left:1050px;top:555px" width="20" height="28" viewBox="0 0 20 28" aria-label="Next" role="img"><path d="M3 2l13 12L3 26" fill="none" stroke="#999" stroke-width="3"/></svg>

    <article class="abs card" style="left:130px;top:590px">
      <div class="card-frame">
        <div class="sale-tag">SALE</div>
        <div class="sale-foot">25%<br><b>Sale</b></div>
        <div class="card-photo" style="left:80px;background:linear-gradient(160deg,#f6d1e4,#ffffff 60%,#f2c7da)" role="img" aria-label="White and pink baby sleeping bag with bear print"></div>
      </div>
      <h3 class="card-name">Baby Sleeping Bag - 1</h3>
      <p class="card-desc">Let your baby sleep with utmost comfort!!</p>
      <p class="card-price">$ 25</p>
      <div class="card-actions"><span class="btn btn-cart">Add to cart</span><span class="btn btn-info">More Info</span></div>
    </article>

    <article class="abs card" style="left:370px;top:590px">
      <div class="card-frame">
        <div class="card-photo" style="left:74px;width:68px;border-radius:34px;background:linear-gradient(180deg,#e0c6a5,#f1e3cf 60%,#d8bfa0)" role="img" aria-label="Beige animal-shaped baby sleeping bag"></div>
      </div>
      <h3 class="card-name">Baby Sleeping Bag - 2</h3>
      <p class="card-desc">Let your baby sleep with utmost comfort!!</p>
      <p class="card-price">$ 25</p>
      <div class="card-actions"><span class="btn btn-cart">Add to cart</span><span class="btn btn-info">More Info</span></div>
    </article>

    <article class="abs card" style="left:609px;top:590px">
      <div class="card-frame">
        <div class="sale-tag">SALE</div>
        <div class="sale-foot">25%<br><b>Sale</b></div>
        <div class="card-photo" style="left:90px;width:64px;background:linear-gradient(180deg,#7fd0f0,#a8e2f7 60%,#6fc4ea)" role="img" aria-label="Light blue zip-up baby sleeping bag"></div>
      </div>
      <h3 class="card-name">Baby Sleeping Bag - 3</h3>
      <p class="card-desc">Let your baby sleep with utmost comfort!!</p>
      <p class="card-price">$ 25</p>
      <div class="card-actions"><span class="btn btn-cart">Add to cart</span><span class="btn btn-info">More Info</span></div>
    </article>

    <article class="abs card" style="left:851px;top:590px">
      <div class="card-frame" style="width:219px">
        <div class="card-photo" style="left:76px;width:62px;background:linear-gradient(170deg,#f4b7d4,#f7c8de 60%,#ee9fc6)" role="img" aria-label="Pink wrap baby sleeping bag"></div>
      </div>
      <h3 class="card-name">Baby Sleeping Bag -4</h3>
      <p class="card-desc">Let your baby sleep with utmost comfort!!</p>
      <p class="card-price">$ 25</p>
      <div class="card-actions" style="width:219px"><span class="btn btn-cart">Add to cart</span><span class="btn btn-info">More Info</span></div>
    </article>
  </section>

  <section>
    <h2 class="abs section-title script" style="left:143px;top:902px;font-weight:400">What's New</h2>
    <h2 class="abs section-title script" style="left:465px;top:902px;font-weight:400">Newsletter</h2>
    <h2 class="abs section-title script" style="left:790px;top:902px;font-weight:400">Special Offers</h2>

    <div class="abs promo" style="left:145px">
      <div class="new-photo" role="img" aria-label="Quilted grey baby sleeping bag on a hanger"></div>
      <div class="new-panel">
        <div class="l1">NEW <em>BABY</em></div>
        <div class="l2">SLEEPING</div>
        <div class="l3">BAG</div>
        <div class="buy">Buy Now</div>
      </div>
    </div>

    <div class="abs promo" style="left:465px">
      <svg class="abs" style="left:19px;top:20px" width="29" height="19" viewBox="0 0 29 19" aria-hidden="true"><rect x="1" y="1" width="27" height="17" fill="none" stroke="#bbb" stroke-width="2"/><path d="M1 1l13.5 10L28 1" fill="none" stroke="#bbb" stroke-width="2"/></svg>
      <div class="abs nl-head">SIGN UP NEWSLETTER</div>
      <p class="abs nl-copy">Lorem Ipsum is simply dummy text of the printing and typesetting industry.</p>
      <div class="abs nl-input">Enter the E-mail Address</div>
      <div class="abs nl-submit">SUBMIT</div>
    </div>

    <div class="abs promo" style="left:786px">
      <div class="offer-photo" role="img" aria-label="Photo of a baby playing with toys on a rug in a bright room"></div>
      <div class="offer-badge">
        <div class="o1">25% OFF</div>
        <div class="o2">ON SLEEPING</div>
        <div class="o3">BAGS</div>
      </div>
    </div>
  </section>

  <footer class="abs footer">
    <div class="abs foot-links">
      <span>Home</span>|<span>About Us</span>|<span>Sleeping Bags</span>|<span>Gifts</span>|<span>Sale</span>|<span>Contact Us</span>
    </div>
    <p class="abs foot-copy">© 2013 Nestlyn ,All&nbsp; rights reserved</p>
    <div class="abs social" role="img" aria-label="Social network links"><i></i><i></i><i></i><i></i></div>
  </footer>

</div>
</body>
</html>
```